Packaging design for a reclosable bag for our product

We have a logo, and we need to put it on packaging for our product and while we want the look to be simple, we want it to follow good design principles and also contain spaces for other product descriptions.

There will be 5 sizes at launch so I'd like 5 variations, one for each size.

I've included a few mockups of the type of bag that I made but they are all just rough ideas that I had.

I want the brand to look scientific and methodical and even a bit quirky, as in "wow this is a serious product but also a bit unusual."

```html
<!DOCTYPE html>
<html lang="en">
<head>
<meta charset="utf-8">
<title>QZ4 Bias Lighting – Pouch Front</title>
<link rel="stylesheet" href="https://fonts.googleapis.com/css2?family=Exo+2:wght@400;600;700;800&display=swap">
<style>
  :root {
    --backdrop: #cdcdcd;
    --pouch: #0a0a0a;
    --pouch-edge: #181818;
    --ink: #ffffff;
    --ink-soft: #ececec;
    --glow: rgba(255,255,255,0.20);
    --seam: #222222;
  }
  * { margin: 0; padding: 0; box-sizing: border-box; }
  html, body { width: 1200px; height: 1200px; overflow: hidden; }
  body {
    background: var(--backdrop);
    font-family: "Exo 2", Arial, sans-serif;
    color: var(--ink);
    position: relative;
  }
  .pouch {
    position: absolute;
    left: 266px; top: 178px;
    width: 668px; height: 866px;
    background:
      radial-gradient(ellipse 260px 170px at 50% 43%, var(--glow), transparent 72%),
      var(--pouch);
    border: 1px solid var(--pouch-edge);
    border-radius: 4px;
  }
  .pouch__notch {
    position: absolute; top: 30px;
    width: 8px; height: 8px;
    background: var(--backdrop);
    border-radius: 50%;
  }
  .pouch__notch--left { left: -4px; }
  .pouch__notch--right { right: -4px; }
  .pouch__zip {
    position: absolute;
    left: 36px; right: 36px; top: 80px;
    height: 3px;
    background: var(--seam);
  }
  .brand {
    position: absolute;
    left: 0; right: 0; top: 290px; height: 174px;
    display: flex; justify-content: center; align-items: center; gap: 20px;
  }
  .brand__mark {
    width: 30px; height: 30px;
    background: var(--ink);
  }
  .brand__name {
    font-weight: 800;
    font-size: 180px;
    line-height: 1;
    color: var(--ink);
  }
  .product-title {
    position: absolute;
    left: 0; right: 0; top: 526px;
    text-align: center;
    font-weight: 700;
    font-size: 56px;
    line-height: 56px;
    letter-spacing: 1px;
    color: var(--ink-soft);
  }
  .product-spec {
    position: absolute;
    left: 120px; top: 602px;
    width: 408px; height: 42px;
    border: 2px solid var(--ink-soft);
    display: flex; align-items: center; justify-content: center;
    font-weight: 400;
    font-size: 25px;
    letter-spacing: 0.4px;
    color: var(--ink-soft);
  }
  .features {
    position: absolute;
    left: 120px; top: 664px;
    display: flex; align-items: stretch; gap: 9px;
    height: 76px;
  }
  .feature {
    background: var(--ink-soft);
    color: var(--pouch);
    border-radius: 7px;
    display: flex; flex-direction: column; align-items: center; justify-content: space-between;
    padding: 6px 4px 5px;
    font-size: 12.5px; font-weight: 600;
    white-space: nowrap;
  }
  .feature svg { display: block; }
  .feature--d65 { width: 79px; }
  .feature--remote { width: 113px; }
  .feature--cri { width: 80px; }
  .size {
    display: flex; flex-direction: column; justify-content: center;
    border-left: 2px solid var(--ink-soft);
    padding-left: 6px; margin-left: 1px;
  }
  .size__value {
    font-size: 68px; font-weight: 600; line-height: 0.85;
    color: var(--ink-soft);
  }
  .size__label {
    margin-top: 4px;
    background: var(--ink-soft); color: var(--pouch);
    font-size: 11px; font-weight: 800; letter-spacing: 0.3px;
    padding: 1px 4px;
    white-space: nowrap;
  }
</style>
</head>
<body>
  <main class="pouch">
    <span class="pouch__notch pouch__notch--left"></span>
    <span class="pouch__notch pouch__notch--right"></span>
    <div class="pouch__zip"></div>

    <div class="brand">
      <span class="brand__mark"></span>
      <span class="brand__name">QZ4</span>
    </div>

    <h1 class="product-title">BIAS LIGHTING</h1>
    <p class="product-spec">6500K WHITE BIAS LIGHTING</p>

    <section class="features">
      <div class="feature feature--d65">
        <svg width="46" height="46" viewBox="0 0 44 44" aria-hidden="true">
          <g stroke="#0a0a0a" stroke-width="2" stroke-linecap="round">
            <line x1="22" y1="2" x2="22" y2="7"/><line x1="22" y1="37" x2="22" y2="42"/>
            <line x1="2" y1="22" x2="7" y2="22"/><line x1="37" y1="22" x2="42" y2="22"/>
            <line x1="8" y1="8" x2="11.5" y2="11.5"/><line x1="32.5" y1="32.5" x2="36" y2="36"/>
            <line x1="36" y1="8" x2="32.5" y2="11.5"/><line x1="8" y1="36" x2="11.5" y2="32.5"/>
          </g>
          <circle cx="22" cy="22" r="11" fill="#0a0a0a"/>
          <text x="22" y="25.5" text-anchor="middle" font-family="Exo 2, sans-serif" font-size="9" font-weight="700" fill="#ececec">D65</text>
        </svg>
        <span>Simulated</span>
      </div>

      <div class="feature feature--remote">
        <svg width="46" height="46" viewBox="0 0 44 44" aria-hidden="true">
          <g fill="none" stroke="#0a0a0a" stroke-width="2" stroke-linecap="round">
            <path d="M12 9 A14 14 0 0 1 32 9"/>
            <path d="M16 13 A8 8 0 0 1 28 13"/>
          </g>
          <rect x="16" y="17" width="12" height="26" rx="2" fill="#0a0a0a"/>
          <g fill="#ececec">
            <circle cx="22" cy="22" r="1.6"/>
            <rect x="19" y="27" width="2" height="2"/><rect x="23" y="27" width="2" height="2"/>
            <rect x="19" y="31" width="2" height="2"/><rect x="23" y="31" width="2" height="2"/>
          </g>
        </svg>
        <span>Wireless Control</span>
      </div>

      <div class="feature feature--cri">
        <svg width="46" height="46" viewBox="0 0 46 46" aria-hidden="true">
          <circle cx="23" cy="23" r="19" fill="none" stroke="#0a0a0a" stroke-width="7" stroke-dasharray="5.5 2"/>
          <circle cx="23" cy="23" r="12" fill="#0a0a0a"/>
          <text x="23" y="26.5" text-anchor="middle" font-family="Exo 2, sans-serif" font-size="9" font-weight="700" fill="#ececec">CRI</text>
        </svg>
        <span>90+</span>
      </div>

      <div class="size">
        <span class="size__value">5m</span>
        <span class="size__label">EXTRA LARGE</span>
      </div>
    </section>
  </main>
</body>
</html>
```